Elegant and modern Wedding Photography brochure

My existing brochure (attached) needs a major facelift. This is one of the main selling tools - it gets emailed to my clients when they make an equiry on what packages i offer and it is printed out and walked through at our first meeting. This brochure is as critical as my website - it needs to sing!

I'm looking for an eye-catching design that says:
Elegant
Modern
Clean
Crisp
Not cutesy or lovey-dovey thanks - we are more sophisticated and professional than that.

Update images to some of the latest weddings I've shot also. Let me know files and resolution you need. I've enabled right-click to download images on my site for a limited time. Please note that I retain copyright and will pursue any breeches.

Http://www.sarahkelbrin.com/Melbourne-wedding-photography
Updates

Thanks for all of your designs! Will take a few days to decide.

Target Market(s)

Australian Women aged 24-44

Industry/Entity Type

Wedding

Font styles to use
Other font styles liked:
• Century Gothic

Requirements
Must have
• Easy to print - does not have to be 6 A4 pages like the existing brochure
Nice to have
• Some full page images - The photos are supposed to be the hero here :-)
Should not have
• Not cutesy or lovey-dovey thanks - we are more sophisticated and professional than that.

No black backgrounds, I prefer a white thanks

No images in organic shaped boxes (like the rectangles in the logo - no thanks).
Keep the lines straight and sharp

```html
<!DOCTYPE html>
<html lang="en">
<head>
<meta charset="utf-8">
<title>Sarah Kelbrin – Wedding Packages Brochure</title>
<link href="https://fonts.googleapis.com/css2?family=Didact+Gothic&family=Quicksand:wght@600;700&family=Tinos&display=swap" rel="stylesheet">
<style>
:root{
  --plum:#7c2a80;
  --plum-soft:#a46aa6;
  --ink:#333;
  --grey:#7a7a7a;
  --paper:#fff;
  --stage:#e4e1e3;
  --photo-green:#7d8f5c;
  --photo-warm:#c9b49a;
  --photo-sea:#9fc3c9;
}
*{box-sizing:border-box;margin:0;padding:0}
html,body{width:1200px;height:927px;overflow:hidden}
body{background:var(--stage);font-family:"Didact Gothic",sans-serif;color:var(--ink);position:relative}
.sheet{position:absolute;background:var(--paper);box-shadow:0 1px 4px rgba(0,0,0,.12);overflow:hidden}
.photo{position:absolute;border-radius:0}
.heading{font-family:"Quicksand",sans-serif;font-weight:700;color:var(--plum)}
.sub{font-family:"Quicksand",sans-serif;font-weight:700;color:var(--plum);font-size:7.5px;margin:6px 0 2px}
.copy{font-size:6.6px;line-height:1.35}
.footer{position:absolute;left:18px;right:18px;bottom:12px;border-top:1.5px solid var(--plum);padding-top:3px;font-size:5.4px;color:var(--plum)}
.brand{color:var(--plum-soft);font-family:"Didact Gothic",sans-serif;font-weight:400}

/* cover spread */
.cover{left:20px;top:20px;width:560px;height:390px}
.cover-back{position:absolute;left:0;top:0;width:280px;height:100%;border-right:1px solid #ddd;padding:70px 30px}
.quote{font-size:10.5px;line-height:1.4;color:#444;margin-bottom:16px}
.cover-back .brand{position:absolute;left:30px;bottom:88px;font-size:18px}
.cover-contact{position:absolute;left:30px;bottom:40px;font-size:9px;color:var(--grey);line-height:1.5}
.cover-front{position:absolute;left:280px;top:0;width:280px;height:100%;text-align:center}
.cover-front .brand{margin-top:140px;font-size:18px}
.cover-title{margin-top:26px;font-size:24px}

/* approach */
.approach{left:600px;top:20px;width:280px;height:390px;padding:22px 18px}
.approach .heading{font-size:18px}
.tagline{font-size:8px;margin-bottom:6px}
.cols{display:flex;gap:10px}
.cols>div{flex:1}

.image-page{left:890px;top:20px;width:290px;height:390px;padding:16px 18px}
.image-page .text{width:128px}

/* a la carte */
.carte{left:20px;top:432px;width:270px;height:475px;padding:26px 22px}
.carte .heading{font-size:18px}
.carte .heading small{font-family:"Didact Gothic",sans-serif;font-weight:400;font-size:8px;color:var(--ink)}
.fee{font-family:"Tinos",serif;font-size:6.6px;line-height:1.35;margin-bottom:8px}
.fee b{display:block;font-family:"Quicksand",sans-serif;color:var(--plum);font-size:7px}

/* remember */
.remember{left:305px;top:432px;width:270px;height:475px;padding:18px}
.remember .heading{font-family:"Didact Gothic",sans-serif;font-weight:400;font-size:19px;line-height:1.2;margin:170px 0 14px}
.remember p{font-size:7px;line-height:1.4;margin-bottom:8px}

/* packages spread */
.packages{left:590px;top:432px;width:590px;height:475px}
.pkg-page{position:absolute;top:0;height:100%;width:295px;padding:22px 18px}
.pkg-page+.pkg-page{left:295px;border-left:1px solid #ddd}
.packages .heading{font-size:20px}
.pkg{font-size:7px;line-height:1.45}
.pkg h3{font-family:"Quicksand",sans-serif;color:var(--plum);font-size:9px;margin-bottom:1px}
.pkg .price{font-family:"Quicksand",sans-serif;color:var(--plum);font-size:7.5px;margin-bottom:6px}
.pkg ul{list-style:none}
.pkg li{margin-bottom:3px}
</style>
</head>
<body>

<section class="sheet cover">
  <div class="cover-back">
    <p class="quote">“Words can't express my thanks Sarah, I am absolutely in awe of my photos! You've captured my wedding day perfectly; couldn't ask for anything more.”<br>- Tess, Kingsford</p>
    <p class="quote">“Thanks so much for photographing our special day, you did an amazing job and made everyone feel so comfortable. The amount of comments we have had on the photos so far has been wonderful and we couldn't be happier!”<br>- Marnie,<br>Elmhurst</p>
    <div class="brand">Sarah Kelbrin</div>
    <div class="cover-contact">www.sarahkelbrin.com | Mobile: 0400 582 917<br>Email: sarah@sarahkelbrin.com<br>Harlow Street, Kingsford, VIC, 3011</div>
  </div>
  <div class="cover-front">
    <div class="brand">Sarah Kelbrin</div>
    <h1 class="heading cover-title">Wedding Packages</h1>
  </div>
</section>

<section class="sheet approach">
  <h2 class="heading">Sarah's approach…</h2>
  <p class="tagline">Enjoy your special day</p>
  <div class="photo" role="img" aria-label="Bride and groom embracing outdoors" style="left:18px;top:68px;width:244px;height:150px;background:linear-gradient(135deg,var(--photo-green),#c8cfa8)"></div>
  <div class="cols" style="margin-top:160px">
    <div><p class="sub">Style &amp; Approach</p><p class="copy">Sarah can observe and capture your wedding day in the background, quickly and quietly taking photojournalistic pictures rather than directing it if you prefer. Or she can confidently play the role of Art Director and instruct beautiful poses. Either way, what is most important is that her clients are relaxed and having a really great time on their wedding day!</p></div>
    <div><p class="sub">Formal Photography</p><p class="copy">Many of Sarah's clients book her because of the easy-going approach she has. They can get on with having a great time on their day without worrying about formal photography. However, there are occasions when clients do want formal family pictures, and Sarah is more than happy to accommodate their requests.</p><p class="copy" style="margin-top:5px">In order to keep the disruption on the day to a minimum, we recommend that Sarah</p></div>
  </div>
  <div class="footer">www.sarahkelbrin.com · Mobile: 0400 582 917 · Email: sarah@sarahkelbrin.com</div>
</section>

<section class="sheet image-page">
  <div class="text">
    <p class="copy">photographs no more than 6 groups, and a select number of the special couple.</p>
    <p class="sub">Image Presentation</p>
    <p class="copy">The most professional way of presenting clients with their photographs is in an elegantly designed photo book. Sarah's clients only pay one fixed price for the photography, regardless of how many images taken. There are no hard sell procedures to go through, and the completed book is prepared within 2-6 weeks after the wedding day.</p>
    <p class="sub">Time of Year</p>
    <p class="copy">Signature pictures can be taken on overcast days or winter months. Don't worry if the sky is not perfectly blue. In the end, regardless of the weather – it's the timeless mood of the day that Sarah strives to capture.</p>
  </div>
  <div class="photo" role="img" aria-label="Couple portrait in a park" style="left:156px;top:62px;width:106px;height:70px;background:linear-gradient(#4a5a3a,#9aa583)"></div>
  <div class="photo" role="img" aria-label="Bridesmaids walking among trees" style="left:156px;top:138px;width:106px;height:70px;background:linear-gradient(#5f7a3f,#b3c48d)"></div>
  <div class="photo" role="img" aria-label="Wedding party group in a garden" style="left:156px;top:214px;width:106px;height:70px;background:linear-gradient(#4c6238,#8fa46a)"></div>
  <div class="photo" role="img" aria-label="Wedding party on a lawn" style="left:156px;top:290px;width:106px;height:70px;background:linear-gradient(#6f8f3a,#c0d28a)"></div>
  <div class="footer" style="color:transparent">.</div>
</section>

<section class="sheet carte">
  <h2 class="heading">À la Carte Fees <small>to Consider</small></h2>
  <div class="cols" style="margin-top:24px">
    <div>
      <p class="fee"><b>Engagement Session/Pre-wedding Shoot</b>$290 for up to 2 hours of photography on location</p>
      <p class="fee"><b>Digital Negatives</b>$490</p>
      <p class="fee"><b>Extended Coverage</b>$160 per hour</p>
      <p class="fee"><b>Web Gallery &amp; Social Media posting</b>$160</p>
      <p class="fee"><b>Slideshow</b>$250</p>
      <p class="fee"><b>Second Photographer</b>$590</p>
      <p class="fee"><b>Client for life</b>No sitting fees for portrait sessions – Anniversaries, family portraits, etc: $390</p>
    </div>
    <div>
      <p class="fee"><b>Photo Enlargements</b>Quality custom archival prints in a variety of sizes 5x7 up to 8x10 $25, 12.5x18.5 $50</p>
      <p class="fee">Stretched Canvas Prints for your wall. Various sizes available from 16"x20" starting at $395 through to 60"x96" $1500</p>
      <p class="fee">Plus many other options!</p>
      <p class="fee"><b>Professionally Edited Album (Regular)</b>$790</p>
      <p class="fee"><b>Album Upgrade from Regular to Signature Grand</b></p>
      <p class="fee">From Gold Package to Signature Grand: $1150</p>
      <p class="fee">From Platinum Package to Signature Grand: $650</p>
      <p class="fee"><b>Custom Thank-you Cards</b>$150 for 50 cards (174mm x 123mm) including envelopes</p>
    </div>
  </div>
  <div class="footer">www.sarahkelbrin.com · Mobile: 0400 582 917 · Email: sarah@sarahkelbrin.com</div>
</section>

<section class="sheet remember">
  <div class="photo" role="img" aria-label="Couple seated on a park bench among autumn trees" style="left:18px;top:18px;width:234px;height:150px;background:linear-gradient(135deg,#6b5a3c,var(--photo-warm))"></div>
  <h2 class="heading">How do you want to remember</h2>
  <p>Elegant, stunning, fuss-free photography that doesn't cost the earth will capture those memories for a lifetime!</p>
  <p>Wedding photography packages start from $1650 and are fully inclusive of fun-filled creative &amp; journalistic coverage, digital negatives and professionally edited album.</p>
  <p>Contact Sarah today to arrange an informal catch-up, discuss your requirements and find out more about the early booking bonus!</p>
  <div class="footer" style="color:transparent">.</div>
</section>

<section class="sheet packages">
  <div class="pkg-page">
    <h2 class="heading">Wedding Packages</h2>
    <div class="photo" role="img" aria-label="Couple portrait by the sea" style="left:18px;top:70px;width:120px;height:100px;background:linear-gradient(var(--photo-sea),#e8eef0)"></div>
    <div class="photo" role="img" aria-label="Groom kissing bride's cheek" style="left:18px;top:176px;width:120px;height:100px;background:linear-gradient(#7fb2bc,#d8c3b4)"></div>
    <div class="photo" role="img" aria-label="Bridal bouquet of pale pink roses" style="left:18px;top:282px;width:120px;height:100px;background:linear-gradient(#f1ecec,#d9c4c6)"></div>
    <div class="pkg" style="position:absolute;left:152px;top:70px;width:125px">
      <h3>SIGNATURE</h3>
      <p class="price">Price: $3650<br>($5540 value)</p>
      <ul>
        <li>Up to 8 hrs of coverage</li>
        <li>Signature Grand (A3) Album with Lay-flat 300g paper, front page, choice of premium linen or leather cover, presentation box, name embossing, up to 52 pages</li>
        <li>Custom Thank-you Cards with envelopes (50)</li>
        <li>Client for life (no sitting fees)</li>
        <li>Second photographer</li>
        <li>Fusion Slideshow (still + moving images)</li>
        <li>Pre-wedding Shoot</li>
        <li>Web Gallery (online for 6 weeks) &amp; Social media</li>
        <li>High Resolution Digital Negatives*</li>
      </ul>
    </div>
  </div>
  <div class="pkg-page">
    <div class="cols" style="margin-top:48px">
      <div class="pkg">
        <h3>PLATINUM</h3>
        <p class="price">Price: $2300<br>($3340 value)</p>
        <ul>
          <li>Up to 6 hrs of coverage</li>
          <li>Regular (A4) Album with Lay-flat 300g paper, printed cover, dust jacket, presentation box, up to 42 pages</li>
          <li>Slideshow</li>
          <li>Pre-wedding Shoot</li>
          <li>Web Gallery (online for 6 weeks) &amp; Social media</li>
          <li>High Resolution Digital Negatives*</li>
        </ul>
      </div>
      <div class="pkg">
        <h3>GOLD</h3>
        <p class="price">Price: $1650<br>($2080 value)</p>
        <ul>
          <li>Up to 4 hrs of coverage</li>
          <li>Regular (A4) Album with Lay-flat 300g paper, printed cover, dust jacket, presentation box, up to 32 pages</li>
          <li>Web Gallery (online for 6 weeks) &amp; Social media</li>
          <li>High Resolution Digital Negatives*</li>
        </ul>
      </div>
    </div>
    <div class="footer">www.sarahkelbrin.com · Mobile: 0400 582 917 · Email: sarah@sarahkelbrin.com</div>
  </div>
</section>

</body>
</html>
```